Business card for new business

I need a card with fruit and an island vibe. The name of our business is called Coral Dash. The graphics we are getting on our truck is a wave of Fruit with an island beach back ground. The wave is made of fruit and its breaking on the shore of an island with palm trees. We also would like our logo some how put on the card. The back of the card to have our slogan. with an island back ground. Our slogan is Fresh fruit energy for every finish.

Target Market(s)

Athletes, people who workout, sporting events

Contact Information for Business Card

fruit and island is the theme of the card

Font styles to use
Sans Serif

Requirements
Must have
• I need colors to be bright. Fruit must look realistic. Pineapple, coconut, watermelon, strawberry, bananas, kiwi, mango should be among the fruit. Logo should be put on card somehow. back of card should have our slogan. "Fresh fruit energy for every finish".
Nice to have
• If you could please make a wave crashing on the shore of a island beach with palm trees in the back ground.

```html
<!DOCTYPE html>
<html lang="en">
<head>
<meta charset="utf-8">
<title>Coral Dash – Business Card</title>
<link rel="stylesheet" href="https://fonts.googleapis.com/css2?family=Work+Sans:wght@400;500&family=Roboto:wght@400;500&display=swap">
<style>
  :root {
    --backdrop: #2b2b2b;
    --card-white: #ffffff;
    --brand-green: #1f6a4e;
    --text-green: #1d5c45;
    --brand-yellow: #e4e46c;
    --sky-top: #3d6a8a;
    --sky-haze: #6f8fa0;
    --island-green: #2f4a34;
    --sea-light: #5f9c9a;
    --sea-deep: #2e6f78;
    --white: #ffffff;
  }
  * { box-sizing: border-box; margin: 0; padding: 0; }
  html, body { width: 1200px; height: 900px; overflow: hidden; }
  body {
    background: var(--backdrop);
    position: relative;
    font-family: "Work Sans", Arial, sans-serif;
  }
  .card {
    position: absolute;
    left: 261px;
    width: 656px;
    height: 358px;
    border-radius: 24px;
    overflow: hidden;
  }
  .card--front { top: 69px; background: var(--card-white); }
  .card--back { top: 472px; }

  /* Front */
  .brand-mark {
    position: absolute;
    left: 44px;
    top: 164px;
    width: 240px;
    display: flex;
    align-items: center;
    justify-content: center;
    gap: 10px;
  }
  .brand-mark__dot {
    width: 14px; height: 14px; border-radius: 50%;
    background: var(--brand-green);
  }
  .brand-mark__name {
    font-family: "Work Sans", Arial, sans-serif;
    font-weight: 500;
    font-size: 24px;
    letter-spacing: 1px;
    color: var(--brand-green);
  }
  .divider {
    position: absolute;
    left: 316px; top: 92px;
    width: 2px; height: 173px;
    background: var(--brand-green);
  }
  .contact {
    position: absolute;
    left: 369px; top: 88px;
    color: var(--text-green);
  }
  .contact__name {
    font-family: "Roboto", Arial, sans-serif;
    font-size: 26px;
    font-weight: 400;
    color: var(--brand-yellow);
    letter-spacing: 0.5px;
    line-height: 1;
  }
  .contact__role { font-size: 17px; line-height: 22px; margin-top: 2px; letter-spacing: 0.6px; }
  .contact__address { font-size: 17px; margin-top: 10px; line-height: 22px; letter-spacing: 0.8px; }
  .contact__lines { list-style: none; margin-top: 11px; }
  .contact__lines li {
    font-size: 17px; line-height: 22px; letter-spacing: 0.7px;
    display: flex; align-items: center;
  }
  .contact__icon { width: 12px; height: 12px; margin-right: 6px; margin-left: -1px; }

  /* Back */
  .island-scene {
    position: absolute; inset: 0;
    background: linear-gradient(180deg,
      var(--sky-top) 0%,
      var(--sky-haze) 36%,
      var(--island-green) 48%,
      var(--island-green) 56%,
      var(--sea-light) 62%,
      var(--sea-deep) 100%);
  }
  .back-mark {
    position: absolute;
    left: 0; right: 0; top: 164px;
    display: flex; align-items: center; justify-content: center; gap: 10px;
  }
  .back-mark__dot { width: 14px; height: 14px; border-radius: 50%; background: var(--white); }
  .back-mark__name {
    font-family: "Work Sans", Arial, sans-serif;
    font-weight: 500; font-size: 24px; letter-spacing: 1px;
    color: var(--white);
  }
  .slogan {
    position: absolute; left: 0; right: 0; top: 318px;
    text-align: center;
    font-family: "Roboto", Arial, sans-serif;
    font-size: 20px; font-weight: 500; line-height: 26px;
    color: var(--brand-yellow);
    letter-spacing: 0.2px;
  }
</style>
</head>
<body>
  <section class="card card--front">
    <div class="brand-mark">
      <span class="brand-mark__dot"></span>
      <span class="brand-mark__name">CORAL DASH</span>
    </div>
    <div class="divider"></div>
    <div class="contact">
      <h1 class="contact__name">LENA HARWOOD</h1>
      <p class="contact__role">Director</p>
      <p class="contact__address">218 Palmetto Lane<br>Bayview, TX 77590</p>
      <ul class="contact__lines">
        <li>
          <svg class="contact__icon" viewBox="0 0 12 12" aria-hidden="true"><path d="M3 1 L5 3.5 L4 5 Q5 7.5 7 8 L8.5 7 L11 9 L9.5 11 Q3 10 1 2.5 Z" fill="none" stroke="#e4e46c" stroke-width="1"/></svg>
          555 214 7788
        </li>
        <li>
          <svg class="contact__icon" viewBox="0 0 12 12" aria-hidden="true"><rect x="1" y="2.5" width="10" height="7" fill="none" stroke="#e4e46c" stroke-width="1"/><path d="M1 2.5 L6 6.5 L11 2.5" fill="none" stroke="#e4e46c" stroke-width="1"/></svg>
          hello@coraldash.com
        </li>
        <li>
          <svg class="contact__icon" viewBox="0 0 12 12" aria-hidden="true"><circle cx="6" cy="6" r="5" fill="none" stroke="#e4e46c" stroke-width="1"/><ellipse cx="6" cy="6" rx="2.2" ry="5" fill="none" stroke="#e4e46c" stroke-width="0.8"/><path d="M1 6 H11 M2 3.5 H10 M2 8.5 H10" stroke="#e4e46c" stroke-width="0.8"/></svg>
          www.coraldash.com
        </li>
      </ul>
    </div>
  </section>

  <section class="card card--back">
    <div class="island-scene" role="img" aria-label="Photo of a tropical island with palm trees surrounded by turquoise sea under a blue sky"></div>
    <div class="back-mark">
      <span class="back-mark__dot"></span>
      <span class="back-mark__name">CORAL DASH</span>
    </div>
    <p class="slogan">Fresh fruit energy for every finish</p>
  </section>
</body>
</html>
```